Halverstone Minerals Web Design

Require a Web page design for an international mining and private investment company currently based in Dubai, UAE. I would like to view designs that incorporate our current corporate logo design aimed at communicating global business development/expansion across a diversity of commodities within the mining and investment sectors.

We are a global organisation with global experience and strategy with specific business development focus in Africa, Central and South America.

Target Market(s)

Mining industry, finance, fund raising, brokering, private equity and public stock exchanges.

Industry/Entity Type

Mining

Number of Pages Required

5+ page

Font styles to use
Sans Serif

Colors

Designer to choose colors to be used in the design.

Requirements
Must have
• Corporate logo, description of who we are, what we do, corporate mission, vision & strategy.
Nice to have
• Inclusion of images, photos, interactive maps/graphics and video.

```html
<!DOCTYPE html>
<html lang="en">
<head>
<meta charset="utf-8">
<title>Halverstone Minerals</title>
<link href="https://fonts.googleapis.com/css2?family=Montserrat:wght@400;500;600;700&display=swap" rel="stylesheet">
<style>
:root{
  --gold:#c6a55c;
  --gold-dark:#a88a45;
  --ink:#1c1c1c;
  --black:#0d0d0d;
  --text:#555;
  --muted:#8a8a8a;
  --line:#e2e2e2;
  --band:#efefef;
  --white:#fff;
}
*{box-sizing:border-box;margin:0;padding:0}
html,body{width:1200px;height:4401px;overflow:hidden}
body{font-family:'Montserrat',sans-serif;color:var(--text);background:var(--white);position:relative}
.abs{position:absolute}
.brand{display:flex;align-items:center;gap:12px;font-weight:700;color:var(--gold);letter-spacing:.5px}
.brand .mark{width:34px;height:34px;background:var(--gold)}
/* header */
.header{top:0;left:0;width:1200px;height:108px}
.header .brand{position:absolute;left:100px;top:36px;font-size:22px}
.call{position:absolute;left:700px;top:34px;display:flex;align-items:center;gap:12px;font-weight:600;font-size:16px;color:var(--ink)}
.call .ring{width:40px;height:40px;border:2px solid var(--gold);border-radius:50%;display:flex;align-items:center;justify-content:center}
.socials{position:absolute;left:996px;top:36px;display:flex;gap:6px}
.socials span{width:32px;height:32px;border-radius:50%;background:#2f63b5}
.nav{top:108px;left:0;width:1200px;height:50px;border-top:1px solid var(--line);display:flex;justify-content:center;gap:0}
.nav a{display:block;padding:0 22px;line-height:50px;font-size:13px;font-weight:600;color:var(--ink);text-decoration:none}
.nav a.active{background:var(--gold);color:var(--white)}
.nav .search{width:14px;height:14px;border:2px solid var(--gold);border-radius:50%;margin:18px 0 0 20px}
/* hero */
.hero{top:158px;left:0;width:1200px;height:582px;background:linear-gradient(180deg,#3a3326 0%,#6b5534 45%,#1b2634 70%,#0c1420 100%)}
.hero h1{position:absolute;top:200px;width:100%;text-align:center;color:var(--white);font-size:54px;font-weight:700;letter-spacing:1px}
.hero p{position:absolute;top:278px;width:100%;text-align:center;color:var(--white);font-size:17px}
.btn-gold{display:inline-block;background:var(--gold);color:var(--white);font-size:13px;font-weight:600;border-radius:24px;padding:14px 32px}
.hero .btn-gold{position:absolute;left:524px;top:322px}
.arrow-c{position:absolute;top:272px;width:40px;height:40px;border-radius:50%;border:2px solid rgba(255,255,255,.6)}
/* who */
.who-brand{left:100px;top:1030px;font-size:30px;flex-direction:column;align-items:flex-start;gap:16px}
.who-brand .mark{width:70px;height:70px}
.who-rule{left:460px;top:900px;width:2px;height:300px;background:var(--line)}
h2{font-size:40px;font-weight:700;color:var(--ink)}
.who{left:500px;top:890px;width:600px}
.orn{width:600px;height:1px;background:var(--line);margin:16px 0 26px;position:relative}
.orn.center{margin:16px auto 0}
.who p{font-size:13px;line-height:2.4}
.btn-line{display:inline-block;border:2px solid var(--gold);border-radius:24px;padding:12px 30px;font-size:13px;font-weight:600;color:var(--gold);margin-top:30px}
/* mission */
.mv{top:1380px;left:0;width:1200px;height:586px}
.mv .panel{position:absolute;top:140px;width:480px;color:var(--white)}
.mv h3{font-size:32px;font-weight:700;margin-bottom:28px}
.mv p{font-size:13px;line-height:2.2}
.btn-ghost{display:inline-block;border:2px solid var(--white);border-radius:24px;padding:12px 30px;font-size:13px;font-weight:600;margin-top:34px}
.mv .btn-gold{margin-top:34px}
/* what we do */
.section-title{width:100%;text-align:center}
.cards{top:2262px;left:100px;display:flex;gap:20px}
.card{width:320px;height:355px;border:1px solid var(--line);position:relative;text-align:center}
.card .img{height:188px}
.card .icon{position:absolute;left:130px;top:150px;width:60px;height:60px;border-radius:50%;background:var(--white);border:1px solid var(--line)}
.card h4{margin-top:58px;font-size:17px;font-weight:700;color:var(--ink)}
.card p{font-size:13px;line-height:1.9;padding:14px 26px 0}
.card .tag{position:absolute;left:95px;bottom:-16px;width:130px;height:34px;background:var(--gold);color:var(--white);font-size:12px;font-weight:700;line-height:34px;clip-path:polygon(12% 0,88% 0,100% 50%,88% 100%,12% 100%,0 50%)}
.side{position:absolute;width:36px;height:36px;border-radius:50%;border:1px solid #bbb;background:var(--white)}
/* testimonials */
.testi{top:2793px;left:0;width:1200px;height:473px;background:var(--band)}
.quotes{position:absolute;top:214px;left:100px;display:flex;gap:40px}
.quote{width:320px;display:flex;gap:20px}
.avatar{width:68px;height:68px;border-radius:50%;flex:none;background:linear-gradient(135deg,#d9c6b4,#8c7766)}
.quote p{font-size:12px;line-height:1.9}
.quote p:before{content:"\201C";color:var(--gold);font-size:30px;font-weight:700;line-height:0;margin-right:6px;vertical-align:-10px}
.quote .who-n{font-size:11px;font-weight:600;color:var(--ink);margin-top:18px;letter-spacing:.5px}
.quote .role{font-size:11px;color:var(--muted);margin-top:4px}
.stars{color:var(--gold);font-size:20px;letter-spacing:2px;margin-top:14px}
/* contact */
.form{top:3544px;left:147px;width:906px}
.row{display:flex;gap:11px;margin-bottom:18px}
.field{flex:1;height:46px;border:1px solid #cfcfcf;font-size:13px;color:var(--muted);padding:14px 18px}
.field.tall{height:115px}
.submit{display:block;width:375px;height:44px;margin:17px auto 0;background:var(--gold);color:var(--white);font-size:15px;font-weight:700;letter-spacing:1px;text-align:center;line-height:44px}
/* footer */
.footer{top:4002px;left:0;width:1200px;height:340px;background:var(--black);color:var(--white)}
.footer .brand{position:absolute;left:100px;top:78px;font-size:22px}
.fsoc{position:absolute;left:100px;top:170px;display:flex;gap:10px}
.fsoc span{width:36px;height:36px;border-radius:50%;border:2px solid var(--white)}
.fcol{position:absolute;top:72px}
.fcol h5{font-size:19px;font-weight:600;margin-bottom:26px}
.fcol li{list-style:none;font-size:12px;line-height:32px}
.contact-li{display:flex;gap:18px;font-size:12px;line-height:1.6;margin-bottom:22px;width:250px}
.contact-li svg{flex:none}
.copy{top:4342px;left:0;width:1200px;height:59px;background:#1a1a1a;color:#ccc;font-size:12px;text-align:center;line-height:59px}
</style>
</head>
<body>

<header class="abs header">
  <div class="brand"><span class="mark"></span>Halverstone Minerals</div>
  <div class="call">
    <span class="ring"><svg width="18" height="18" viewBox="0 0 24 24"><path d="M6.6 10.8a15 15 0 006.6 6.6l2.2-2.2a1 1 0 011-.25 11.4 11.4 0 003.6.57 1 1 0 011 1V20a1 1 0 01-1 1A17 17 0 013 4a1 1 0 011-1h3.5a1 1 0 011 1 11.4 11.4 0 00.57 3.6 1 1 0 01-.25 1z" fill="#c6a55c"/></svg></span>
    CALL US : 1 800 555 0142
  </div>
  <div class="socials"><span></span><span style="background:#2aa3e0"></span><span style="background:#1c6fb0"></span></div>
</header>

<nav class="abs nav">
  <a class="active">HOME</a><a>WHO WE ARE</a><a>WHAT WE DO</a><a>CORPORATE MISSION</a><a>VISION &amp; STRATEGY</a><a>CONTACT US</a><span class="search"></span>
</nav>

<section class="abs hero" role="img" aria-label="City skyline at dusk with a connected network of lines over the water">
  <span class="arrow-c" style="left:36px"></span><span class="arrow-c" style="left:1124px"></span>
  <h1>HALVERSTONE MINERALS</h1>
  <p>Sed ut perspiciatis unde omnis iste natus error sit voluptatem accusantium</p>
  <span class="btn-gold">READ MORE</span>
  <svg class="abs" style="left:560px;top:548px" width="80" height="34" viewBox="0 0 80 34"><path d="M0 34 L40 0 L80 34Z" fill="#fff"/><path d="M34 16l6 6 6-6" stroke="#222" stroke-width="2" fill="none"/></svg>
</section>

<div class="abs brand who-brand"><span class="mark"></span>Halverstone Minerals</div>
<div class="abs who-rule"></div>
<section class="abs who">
  <h2>Who we are</h2>
  <div class="orn"></div>
  <p>Sed ut perspiciatis unde omnis iste natus error sit voluptatem accusantium doloremque laudantium, totam rem aperiam, eaque ipsa quae ab illo inventore veritatis et quasi architecto beatae vitae dicta sunt explicabo. Nemo enim ipsam voluptatem quia voluptas sit aspernatur aut odit aut fugit, sed quia consequuntur magni dolores eos qui ratione voluptatem sequi nesciunt neque porro quisquam est qui dolorem ipsum quia dolor sit amet consectetur adipisci velit sed quia non numquam.</p>
  <span class="btn-line">READ MORE</span>
</section>

<section class="abs mv">
  <svg class="abs" width="1200" height="586" viewBox="0 0 1200 586">
    <polygon points="0,0 600,58 600,504 0,586" fill="#c6a55c"/>
    <polygon points="600,58 1200,0 1200,586 600,504" fill="#0f0f0f"/>
  </svg>
  <div class="panel" style="left:100px">
    <h3>CORPORATE MISSION</h3>
    <p>At vero eos et accusamus et iusto odio dignissimos ducimus qui blanditiis praesentium voluptatum deleniti atque corrupti quos dolores et quas molestias excepturi sint occaecati cupiditate non provident, similique sunt in culpa qui officia deserunt mollitia animi, id est laborum et dolorum fuga.</p>
    <span class="btn-ghost">READ MORE</span>
  </div>
  <div class="panel" style="left:698px">
    <h3>VISION &amp; STRATEGY</h3>
    <p>At vero eos et accusamus et iusto odio dignissimos ducimus qui blanditiis praesentium voluptatum deleniti atque corrupti quos dolores et quas molestias excepturi sint occaecati cupiditate non provident, similique sunt in culpa qui officia deserunt mollitia animi, id est laborum et dolorum fuga.</p>
    <span class="btn-gold">READ MORE</span>
  </div>
</section>

<section class="abs section-title" style="top:2100px">
  <h2>What we do</h2>
  <div class="orn center"></div>
</section>
<span class="side" style="left:28px;top:2428px"></span>
<span class="side" style="left:1136px;top:2428px"></span>
<div class="abs cards">
  <article class="card">
    <div class="img" role="img" aria-label="Yellow dump truck in a stone quarry" style="background:linear-gradient(160deg,#9aa3a8,#6d6f6a 60%,#c9a21e)"></div>
    <span class="icon"></span>
    <h4>SURFACE MINING</h4>
    <p>Sed ut perspiciatis unde omnis iste natus error sit voluptatem accusantium doloremque</p>
    <span class="tag">READ MORE</span>
  </article>
  <article class="card">
    <div class="img" role="img" aria-label="Loader beside a gravel stockpile" style="background:linear-gradient(160deg,#c8c2b4,#9d8a6c 60%,#b08a3a)"></div>
    <span class="icon"></span>
    <h4>DEEP MINING</h4>
    <p>Sed ut perspiciatis unde omnis iste natus error sit voluptatem accusantium doloremque</p>
    <span class="tag">READ MORE</span>
  </article>
  <article class="card">
    <div class="img" role="img" aria-label="Site engineer in hard hat with a clipboard near heavy machinery" style="background:linear-gradient(160deg,#d8d4cc,#c25a2c 55%,#d6a323)"></div>
    <span class="icon"></span>
    <h4>FORWARD PLANNING</h4>
    <p>Sed ut perspiciatis unde omnis iste natus error sit voluptatem accusantium doloremque</p>
    <span class="tag">READ MORE</span>
  </article>
</div>

<section class="abs testi">
  <div style="position:absolute;top:88px;width:100%;text-align:center"><h2>Client Testimonials</h2><div class="orn center"></div></div>
  <span class="side" style="left:28px;top:286px"></span>
  <span class="side" style="left:1136px;top:286px"></span>
  <div class="quotes">
    <div class="quote"><div class="avatar" role="img" aria-label="Client portrait"></div><div><p>At vero eos et accusamus et iusto odio dignissimos ducimus qui blanditiis praesentium sunt voluptas quo.</p><div class="who-n">MARISA OKAFOR</div><div class="role">Financial Services Professional</div><div class="stars">★★★★☆</div></div></div>
    <div class="quote"><div class="avatar" role="img" aria-label="Client portrait" style="background:linear-gradient(135deg,#cfcfcf,#555)"></div><div><p>At vero eos et accusamus et iusto odio dignissimos ducimus qui blanditiis praesentium sunt voluptas quo.</p><div class="who-n">TEODOR VANCE</div><div class="role">National Urban Fellow at the Institute</div><div class="stars">★★★★★</div></div></div>
    <div class="quote"><div class="avatar" role="img" aria-label="Client portrait" style="background:linear-gradient(135deg,#e4d8cc,#9c8576)"></div><div><p>At vero eos et accusamus et iusto odio dignissimos ducimus qui blanditiis praesentium sunt voluptas quo.</p><div class="who-n">LEILA BRANDT</div><div class="role">Creative Strategist | Entrepreneur</div><div class="stars">★★★★☆</div></div></div>
  </div>
</section>

<section class="abs section-title" style="top:3406px">
  <h2>Contact Form</h2>
  <div class="orn center"></div>
</section>
<form class="abs form">
  <div class="row"><div class="field">Name</div><div class="field">Email</div></div>
  <div class="row"><div class="field">Phone</div><div class="field">Address</div></div>
  <div class="row"><div class="field tall">Message</div></div>
  <span class="submit">SUBMIT MESSAGE</span>
</form>

<footer class="abs footer">
  <div class="brand"><span class="mark"></span>Halverstone Minerals</div>
  <div class="fsoc"><span></span><span></span><span></span><span></span></div>
  <div class="fcol" style="left:460px">
    <h5>Contact Us</h5>
    <div class="contact-li"><svg width="14" height="18" viewBox="0 0 14 18"><path d="M7 0a7 7 0 017 7c0 5-7 11-7 11S0 12 0 7a7 7 0 017-7z" fill="#fff"/><circle cx="7" cy="7" r="2.5" fill="#0d0d0d"/></svg><span>151, Aurel Quay Road, Harbour District, Dubai</span></div>
    <div class="contact-li"><svg width="14" height="14" viewBox="0 0 24 24"><path d="M6.6 10.8a15 15 0 006.6 6.6l2.2-2.2a1 1 0 011-.25 11.4 11.4 0 003.6.57 1 1 0 011 1V20a1 1 0 01-1 1A17 17 0 013 4a1 1 0 011-1h3.5a1 1 0 011 1 11.4 11.4 0 00.57 3.6 1 1 0 01-.25 1z" fill="#fff"/></svg><span>1 800 555 0142</span></div>
    <div class="contact-li"><svg width="14" height="12" viewBox="0 0 14 12"><rect width="14" height="12" fill="#fff"/><path d="M0 0l7 6 7-6" stroke="#0d0d0d" fill="none"/></svg><span>info@halverstoneminerals.com</span></div>
  </div>
  <div class="fcol" style="left:780px">
    <h5>Quick Links</h5>
    <ul><li>Home</li><li>Who we are</li><li>What we do</li><li>Corporate mission</li><li>Vision &amp; strategy</li><li>Contact us</li></ul>
  </div>
  <div class="fcol" style="left:988px">
    <h5>Other Links</h5>
    <ul><li>FAQ</li><li>Support</li><li>Sitemap</li><li>Terms Of Use</li><li>Privacy Statement</li></ul>
  </div>
</footer>
<div class="abs copy">© copyright 2018 · Halverstone Minerals. All Rights Reserved</div>

</body>
</html>
```